Business Card for a Dental Office

The design should communicate integrity, quality and reliability. We also want the card look elegant, simple, but still stand out, different from the traditional-dental-office business card.

Industry/Entity Type

Business

```html
<!DOCTYPE html>
<html lang="en">
<head>
<meta charset="utf-8">
<title>Halden Dental Centre – Business Card</title>
<link rel="stylesheet" href="https://fonts.googleapis.com/css2?family=Oswald:wght@500;600&family=Open+Sans:wght@400;600&display=swap">
<style>
  :root {
    --page-bg: #e9e5dc;
    --card-dark: #7d6220;
    --card-mid: #9a7e33;
    --card-light: #a98d42;
    --white: #ffffff;
    --accent: #e8d84a;
    --muted: #d9cfa6;
    --divider: rgba(255,255,255,0.55);
  }
  html, body {
    margin: 0;
    padding: 0;
    width: 1200px;
    height: 1022px;
    overflow: hidden;
    background: var(--page-bg);
  }
  .business-card {
    position: absolute;
    left: 100px;
    top: 225px;
    width: 1000px;
    height: 572px;
    border-radius: 22px;
    background: linear-gradient(135deg, var(--card-light) 0%, var(--card-mid) 45%, var(--card-dark) 100%);
    box-shadow: 0 18px 40px rgba(60,45,15,0.35);
    overflow: hidden;
    font-family: "Open Sans", Arial, sans-serif;
    color: var(--white);
  }
  .brand {
    position: absolute;
    left: 90px;
    top: 120px;
    display: flex;
    align-items: center;
    gap: 26px;
  }
  .brand-square {
    width: 64px;
    height: 64px;
    background: var(--accent);
    flex: none;
  }
  .brand-name {
    font-family: "Oswald", "Arial Narrow", sans-serif;
    font-weight: 600;
    font-size: 60px;
    line-height: 1;
    letter-spacing: 0.5px;
    text-transform: uppercase;
    margin: 0;
  }
  .tagline {
    font-family: "Open Sans", Arial, sans-serif;
    font-weight: 600;
    font-size: 21px;
    letter-spacing: 2px;
    margin: 10px 0 0;
    color: var(--muted);
    text-transform: uppercase;
  }
  .tagline .highlight { color: var(--accent); }
  .footer-row {
    position: absolute;
    left: 90px;
    bottom: 90px;
    display: flex;
    align-items: center;
    gap: 34px;
  }
  .person-name {
    font-family: "Oswald", "Arial Narrow", sans-serif;
    font-weight: 500;
    font-size: 36px;
    letter-spacing: 1px;
    margin: 0;
    text-transform: uppercase;
  }
  .person-role {
    font-size: 20px;
    letter-spacing: 2px;
    color: var(--accent);
    margin: 4px 0 0;
    text-transform: uppercase;
  }
  .divider {
    width: 2px;
    height: 110px;
    background: var(--divider);
  }
  .contact-list {
    list-style: none;
    margin: 0;
    padding: 0;
    font-size: 22px;
    line-height: 1.6;
  }
  .contact-list li {
    display: flex;
    align-items: center;
    gap: 14px;
  }
  .contact-icon {
    width: 20px;
    height: 20px;
    flex: none;
  }
</style>
</head>
<body>
  <section class="business-card">
    <header class="brand">
      <span class="brand-square"></span>
      <div>
        <h1 class="brand-name">Halden Dental Centre</h1>
        <p class="tagline">Your smile is <span class="highlight">your gift</span> to others</p>
      </div>
    </header>

    <div class="footer-row">
      <div class="person">
        <h2 class="person-name">Marcus Hale</h2>
        <p class="person-role">Director</p>
      </div>
      <span class="divider"></span>
      <ul class="contact-list">
        <li>
          <svg class="contact-icon" viewBox="0 0 20 20" aria-hidden="true">
            <path d="M5 2 L8 2 L9 6 L7 8 Q9 12 12 13 L14 11 L18 12 L18 15 Q18 18 15 18 Q3 16 2 5 Q2 2 5 2 Z" fill="var(--accent)"/>
          </svg>
          <span>+330 5518-2093</span>
        </li>
        <li>
          <svg class="contact-icon" viewBox="0 0 20 20" aria-hidden="true">
            <rect x="2" y="4" width="16" height="12" rx="1.5" fill="var(--accent)"/>
            <path d="M2.5 5 L10 11 L17.5 5" fill="none" stroke="var(--card-mid)" stroke-width="1.6"/>
          </svg>
          <span>info@haldendentalcentre.com</span>
        </li>
        <li>
          <svg class="contact-icon" viewBox="0 0 20 20" aria-hidden="true">
            <circle cx="10" cy="10" r="8" fill="var(--accent)"/>
            <g fill="none" stroke="var(--card-mid)" stroke-width="1.2">
              <ellipse cx="10" cy="10" rx="3.5" ry="8"/>
              <line x1="2" y1="10" x2="18" y2="10"/>
              <line x1="3.5" y1="6" x2="16.5" y2="6"/>
              <line x1="3.5" y1="14" x2="16.5" y2="14"/>
            </g>
          </svg>
          <span>www.haldendentalcentre.com</span>
        </li>
      </ul>
    </div>
  </section>
</body>
</html>
```